Web Design Project

Please take a look at my current aged website www.talvikhrconsulting.com and my newly designed logo and business cards. I would like a new fresh updated look to my website and my new designs incorporated.
Updates

  Good Morning Everyone

Due to an Austrralian licencing issue I have had to have my logo slightly redesigned.

Would you please be able to look at the newly uploaded files and revise your designs.

Thanks so much.  I am very happy with the calibre and quality of the designs so far.

kind Regards

Marla

Industry/Entity Type

Business

Requirements
Must have
• the exisiting pages and fresh new graphics and a real commitment to my palette of lime green, turqouise and black.

```html
<!DOCTYPE html>
<html lang="en">
<head>
<meta charset="utf-8">
<title>Talvik HR Consulting</title>
<link href="https://fonts.googleapis.com/css2?family=Tinos:wght@400;700&family=Merriweather:wght@300;400&display=swap" rel="stylesheet">
<style>
:root{
  --lime:#8dcc6d;
  --turq:#1ba0c2;
  --ink:#111;
  --text:#4a4a4a;
  --muted:#8a8a8a;
  --page:#f1f1f1;
  --band:#e3e3e3;
  --foot:#d9d7d7;
  --field:#e6e6e6;
}
*{margin:0;padding:0;box-sizing:border-box}
html,body{width:872px;height:1200px;overflow:hidden}
body{position:relative;background:var(--page);font-family:"Merriweather",serif;color:var(--text)}
.abs{position:absolute}
.top-bar{left:0;top:6px;width:872px;height:8px;background:var(--lime)}
.header{left:0;top:14px;width:872px;height:138px;background:var(--page)}
.brand{left:45px;top:74px;display:flex;align-items:center;gap:8px;font-family:"Tinos",serif;font-weight:700;font-size:24px;color:var(--turq)}
.brand-dot{width:26px;height:26px;border-radius:50%;background:var(--lime)}
.nav-home{left:315px;top:14px;width:76px;height:110px;background:var(--lime);color:#fff;font-family:"Tinos",serif;font-weight:700;font-size:15px;text-align:center;padding-top:58px}
.nav{top:74px;font-family:"Tinos",serif;font-weight:700;font-size:12.5px;color:var(--ink)}
.hero{left:0;top:152px;width:872px;height:483px;background:var(--band)}
.hero-title{left:0;width:872px;text-align:center;font-family:"Tinos",serif;font-weight:700;font-size:26px}
.hero-title.one{top:156px;color:var(--turq)}
.hero-title.two{top:187px;color:var(--lime)}
.slide{left:45px;top:233px;width:783px;height:351px;background:linear-gradient(180deg,#dfe8ee 0%,#c9d3d9 55%,#8a8f95 100%);border:1px solid #fff}
.arrow{top:385px;width:38px;height:32px;border-radius:50%;background:#fff;border:1px solid #ccc;display:flex;align-items:center;justify-content:center}
.dot{top:593px;width:10px;height:10px;border-radius:50%;background:#ccc}
.section-title{font-family:"Tinos",serif;font-weight:700;font-size:14.5px;color:var(--turq)}
.list{font-size:9.3px;line-height:12.2px;color:var(--text);list-style:none;font-weight:300}
.photo{left:272px;top:716px;width:314px;height:225px;background:linear-gradient(180deg,#e8ecee 0%,#c9cfd4 60%,#9aa0a6 100%);border:1px solid #ccc}
.intro{left:272px;top:958px;width:300px;font-size:9.3px;line-height:12.2px;font-weight:300}
.read-more{left:272px;top:1056px;font-size:9.5px;color:var(--lime)}
.note-icon{left:608px;top:658px;width:60px;height:42px;background:linear-gradient(135deg,#f7e7a2,#e8c96a);transform:rotate(-8deg)}
.form-hint{left:673px;top:672px;width:160px;font-family:"Tinos",serif;font-weight:700;font-size:10.5px;line-height:12.5px;color:var(--turq)}
.form{left:608px;top:716px;width:219px;height:349px;border:1px solid #ccc;border-radius:6px;background:linear-gradient(180deg,#ececec,#e2e2e2);padding:4px 12px}
.form label{display:block;font-family:"Tinos",serif;font-size:11px;color:#333;margin-top:0}
.form .field{display:block;height:23px;border:1px solid #bbb;border-radius:3px;background:var(--field);box-shadow:inset 0 1px 3px rgba(0,0,0,.2);margin:4px 0 6px}
.form .area{height:92px}
.submit{display:block;margin:6px auto 0;width:62px;height:26px;border-radius:5px;background:linear-gradient(#555,#111);color:#fff;font-family:"Tinos",serif;font-weight:700;font-size:11px;border:none}
.footer{left:0;top:1117px;width:872px;height:83px;background:var(--foot)}
.foot-links{left:0;top:1146px;width:872px;display:flex;justify-content:center;gap:24px;font-family:"Tinos",serif;font-size:12px;color:var(--muted)}
.copyright{left:0;top:1169px;width:872px;text-align:center;font-family:"Tinos",serif;font-size:12px;color:var(--muted)}
</style>
</head>
<body>
<div class="abs top-bar"></div>
<header class="abs header"></header>
<div class="abs brand"><span class="brand-dot"></span>Talvik Consulting</div>
<div class="abs nav-home">Home</div>
<div class="abs nav" style="left:422px">Our Services</div>
<div class="abs nav" style="left:532px">Our Consultants</div>
<div class="abs nav" style="left:661px">Our Fees</div>
<div class="abs nav" style="left:752px">Contact US</div>

<section class="abs hero"></section>
<h1 class="abs hero-title one">Talvik HR Consulting</h1>
<h2 class="abs hero-title two">Outsourced Human Resources Solutions and Strategies</h2>
<div class="abs slide" role="img" aria-label="Photo of a presenter at a flip chart with colleagues around a meeting table"></div>
<div class="abs arrow" style="left:46px"><svg width="8" height="10"><path d="M6 1L2 5l4 4" stroke="#555" fill="none" stroke-width="1.4"/></svg></div>
<div class="abs arrow" style="left:789px"><svg width="8" height="10"><path d="M2 1l4 4-4 4" stroke="#555" fill="none" stroke-width="1.4"/></svg></div>
<div class="abs dot" style="left:413px;width:13px;height:12px;top:592px;background:var(--lime)"></div>
<div class="abs dot" style="left:432px"></div>
<div class="abs dot" style="left:448px"></div>

<h3 class="abs section-title" style="left:45px;top:669px">People Systems and Processes</h3>
<ul class="abs list" style="left:45px;top:706px">
<li>Attraction, Recruitment and Induction</li><li>Remuneration, Benefits and Salary</li><li>Talent Management and Retention</li><li>Graduate Management</li><li>Performance Management and Planning</li><li>Conflict, Dispute and Grievance</li><li>Facilitation and Resolution Workforce Planning</li><li>Reward and Recognition</li><li>Leadership Programs</li><li>Career Counselling</li><li>Coaching and Mentoring</li>
</ul>
<h3 class="abs section-title" style="left:45px;top:854px">Employee Relations</h3>
<ul class="abs list" style="left:46px;top:882px">
<li>HR Function Review and Assessments</li><li>Industrial Relations advice</li><li>Contracts of Employment</li><li>Industrial Award Service</li><li>Employee Entitlements</li><li>Equal Opportunity</li><li>Union issues</li><li>Termination</li>
</ul>
<h3 class="abs section-title" style="left:45px;top:992px">Organisation Development</h3>
<ul class="abs list" style="left:46px;top:1024px">
<li>Policy &amp; Procedure Development and Auditing</li><li>Organisation Evaluation and Re-design</li><li>Culture and Values Asssessment and Planning</li>
</ul>

<h3 class="abs section-title" style="left:272px;top:669px">What can Talvik HR Consulting do for me?</h3>
<div class="abs photo" role="img" aria-label="Photo of three smiling colleagues meeting at a desk"></div>
<p class="abs intro">During these challenging economic times it can be difficult to justify internal human resources management services or support. However as a business owner or Manager you may find that HR support or advice is required from time to time. Talvik HR Consulting are an outsourced HR function.&nbsp; We can provide you with that ongoing support, offer solutions and assist you with developing strategies that fit your business an deliver results.</p>
<div class="abs read-more">READ MORE <svg width="8" height="6"><path d="M0 3h6M4 1l2 2-2 2" stroke="#8dcc6d" fill="none"/></svg></div>

<div class="abs note-icon" role="img" aria-label="Illustration of a notepad and pencil"></div>
<div class="abs form-hint">Please fill out the form below and a Consultant will be in touch shortly</div>
<form class="abs form">
<label>First Name:</label><span class="field"></span>
<label>Last Name:</label><span class="field"></span>
<label>Company:</label><span class="field"></span>
<label>Email:</label><span class="field"></span>
<label>Phone:</label><span class="field"></span>
<label>Comments:</label><span class="field area"></span>
<button type="button" class="submit">Submit</button>
</form>

<footer class="abs footer"></footer>
<nav class="abs foot-links"><span>Home</span><span>Our Services</span><span>Our Consultants</span><span>Our Fees</span><span>Contact us</span></nav>
<div class="abs copyright">TalvikConsulting©2012 Privacy Policy</div>
</body>
</html>
```